Halverstone Minerals Web Design

Require a Web page design for an international mining and private investment company currently based in Dubai, UAE. I would like to view designs that incorporate our current corporate logo design aimed at communicating global business development/expansion across a diversity of commodities within the mining and investment sectors.

We are a global organisation with global experience and strategy with specific business development focus in Africa, Central and South America.

Target Market(s)

Mining industry, finance, fund raising, brokering, private equity and public stock exchanges.

Industry/Entity Type

Mining

Number of Pages Required

5+ page

Font styles to use
Sans Serif

Colors

Designer to choose colors to be used in the design.

Requirements
Must have
• Corporate logo, description of who we are, what we do, corporate mission, vision & strategy.
Nice to have
• Inclusion of images, photos, interactive maps/graphics and video.

```html
<!DOCTYPE html>
<html lang="en">
<head>
<meta charset="utf-8">
<title>Halverstone Minerals</title>
<link href="https://fonts.googleapis.com/css2?family=Poppins:wght@400;500;600;700&family=Roboto:wght@400;500;700&display=swap" rel="stylesheet">
<style>
:root{
  --gold:#b8974a;
  --gold-dark:#a5843a;
  --ink:#1c1c1c;
  --text:#444;
  --muted:#666;
  --dark:#161616;
  --dark-2:#202020;
  --light:#eeeeee;
  --white:#fff;
}
*{margin:0;padding:0;box-sizing:border-box}
html,body{width:1200px;height:4186px;overflow:hidden}
body{position:relative;font-family:"Poppins",sans-serif;color:var(--text);background:var(--white)}
.abs{position:absolute}
.btn{position:absolute;display:flex;align-items:center;justify-content:center;background:var(--gold);color:var(--white);font-family:"Roboto",sans-serif;font-weight:700;font-size:15px;letter-spacing:1px;text-transform:uppercase;border-radius:22px}
.photo{position:absolute}

/* hero */
.hero{position:absolute;left:0;top:0;width:1200px;height:698px;background:linear-gradient(160deg,#2b2a27 0%,#1b1b1a 40%,#3a3326 70%,#1a1918 100%)}
.brand{position:absolute;display:flex;align-items:center;gap:12px;color:var(--white);font-family:"Poppins",sans-serif;font-weight:600}
.brand .mark{width:40px;height:40px;background:var(--gold)}
.brand span{font-size:17px;letter-spacing:1px;text-transform:uppercase}
.topbar{position:absolute;right:130px;top:42px;display:flex;gap:34px;color:var(--white);font-family:"Roboto",sans-serif;font-size:17px;align-items:center}
.topbar .item{display:flex;align-items:center;gap:10px}
.nav{position:absolute;right:130px;top:96px;display:flex;gap:24px;color:var(--white);font-family:"Roboto",sans-serif;font-size:13px;font-weight:500;text-transform:uppercase}
.hero h1{position:absolute;left:0;width:1200px;top:272px;text-align:center;color:var(--white);font-family:"Roboto",sans-serif;font-weight:700;font-size:50px;line-height:64px}
.hero h1 .light{font-weight:400;display:block}
.dots{position:absolute;top:506px;left:563px;display:flex;gap:8px;align-items:center}
.dots i{width:12px;height:12px;border-radius:50%;background:var(--white)}
.dots i.on{width:18px;height:18px;border:3px solid var(--white);background:transparent}

/* what we do */
.section-title{position:absolute;left:0;width:1200px;text-align:center;font-family:"Poppins",sans-serif;font-size:42px;font-weight:500;color:var(--ink)}
.section-title .accent{color:var(--gold)}
.lead{position:absolute;left:200px;width:800px;text-align:center;font-size:13px;line-height:28px;color:var(--muted)}
.service{position:absolute;width:240px;text-align:center}
.service svg{display:block;margin:0 auto}
.service h3{margin-top:22px;font-family:"Roboto",sans-serif;font-size:18px;font-weight:500;color:var(--ink)}
.service p{margin-top:10px;font-size:12px;line-height:22px;color:var(--muted)}

/* dark story */
.story{position:absolute;left:0;top:1242px;width:1200px;height:1214px;background:linear-gradient(180deg,#161616,#1e1c19 50%,#151515)}
.frame{position:absolute;border:12px solid #8f8f8f}
.story h2{position:absolute;font-family:"Poppins",sans-serif;font-weight:600;font-size:36px;color:var(--gold);letter-spacing:1px}
.story p{position:absolute;width:480px;color:#ddd;font-size:13px;line-height:28px}

/* clients */
.clients{position:absolute;left:0;top:2456px;width:1200px;height:474px;background:var(--light)}
.quote{position:absolute;width:310px}
.quote .q{color:var(--gold);font-size:44px;font-family:"Roboto",sans-serif;font-weight:700;line-height:30px}
.quote p{margin-top:10px;font-size:12px;line-height:20px;color:#555}
.person{display:flex;align-items:center;gap:14px;margin-top:20px}
.avatar{width:72px;height:72px;border-radius:50%;border:3px solid #ccc;background:linear-gradient(135deg,#9a9a9a,#555)}
.person b{display:block;color:var(--gold);font-weight:500;font-size:15px}
.person small{display:block;font-size:11px;color:#777}
.person .stars{color:#333;font-size:14px;letter-spacing:3px}

/* news */
.news{position:absolute;width:293px}
.news .img{height:187px}
.news .meta{margin-top:26px;padding-left:16px;border-left:4px solid #999}
.news .date{font-size:12px;color:#333}
.news .title{margin-top:8px;font-size:13px;line-height:24px;color:#333}

/* partners */
.partners{position:absolute;left:0;top:3530px;width:1200px;height:140px;background:#f2f2f2}
.partners .row{position:absolute;left:180px;width:860px;top:48px;display:flex;justify-content:space-between;align-items:center;color:#888;font-family:"Roboto",sans-serif;font-weight:700;font-size:26px}

/* footer */
.footer{position:absolute;left:0;top:3655px;width:1200px;height:531px;background:var(--dark)}
.footer h4{position:absolute;top:158px;color:var(--white);font-family:"Poppins",sans-serif;font-weight:600;font-size:22px}
.footer h4 .accent{color:var(--gold)}
.links{position:absolute;left:131px;top:210px;list-style:none;color:#ccc;font-size:13px;line-height:24px}
.links li::before{content:"›";margin-right:12px;color:#ccc}
.contact{position:absolute;left:346px;top:212px;color:#ccc;font-size:12px;line-height:19px}
.contact .row{display:flex;gap:14px;margin-bottom:16px}
.signup-text{position:absolute;left:664px;top:206px;width:280px;color:#ccc;font-size:11px;line-height:18px}
.field{position:absolute;left:664px;top:262px;width:310px;height:40px;background:var(--white);border-radius:20px;font-size:11px;color:#666;padding-left:20px;display:flex;align-items:center}
.field .btn{right:0;top:0;width:100px;height:40px;font-size:11px;border-radius:20px}
.social{position:absolute;left:664px;top:322px;display:flex;gap:8px}
.social i{width:26px;height:26px;border-radius:50%;border:1.5px solid #aaa}
.rule{position:absolute;left:131px;top:419px;width:938px;height:1px;background:#333}
.copy{position:absolute;right:131px;top:462px;color:#ccc;font-size:12px}
</style>
</head>
<body>

<header class="hero" role="img" aria-label="Dark aerial photograph of an open-pit mine with a yellow excavator">
  <div class="brand" style="left:131px;top:64px"><div class="mark"></div><span>Halverstone Minerals</span></div>
  <div class="topbar">
    <div class="item">
      <svg width="30" height="30" viewBox="0 0 30 30"><circle cx="15" cy="15" r="13" fill="none" stroke="#fff" stroke-width="1.5"/><path d="M10 9c1 5 4 9 10 11l2-3-3-2-2 1c-2-1-3-3-4-5l1-2-2-3z" fill="#fff"/></svg>
      555-210-4478
    </div>
    <div class="item">
      <svg width="30" height="30" viewBox="0 0 30 30"><circle cx="15" cy="15" r="13" fill="none" stroke="#fff" stroke-width="1.5"/><rect x="8" y="10" width="14" height="10" fill="none" stroke="#fff" stroke-width="1.5"/><path d="M8 10l7 6 7-6" fill="none" stroke="#fff" stroke-width="1.5"/></svg>
      info@halverstoneminerals.com
    </div>
  </div>
  <nav class="nav"><span>Home</span><span>Who We Are</span><span>What We Do</span><span>Corporate Mission</span><span>Vision &amp; Strategy</span><span>Contact Us</span></nav>
  <h1>International Mining and <span class="light">Private Investment</span></h1>
  <div class="btn" style="left:491px;top:428px;width:218px;height:40px;font-size:14px">Request a Quote</div>
  <div class="dots"><i class="on"></i><i></i><i></i><i></i></div>
</header>

<section>
  <h2 class="section-title" style="top:758px"><span class="accent">What</span> We Do</h2>
  <p class="lead" style="top:826px">Sed ut perspiciatis unde omnis iste natus error sit voluptatem accusantium doloremque laudantium, totam rem aperiam, eaque ipsa quae ab illo inventore veritatis et quasi architecto beatae vitae dicta sunt explicabo.</p>

  <div class="service" style="left:112px;top:950px">
    <svg width="80" height="80" viewBox="0 0 80 80" fill="none" stroke="#333" stroke-width="2"><path d="M14 30q26-24 52 0"/><path d="M40 18L18 66"/><circle cx="56" cy="50" r="14" stroke="#b8974a"/><path d="M52 43v14M52 43h5a3 3 0 010 7h-5h6a3 3 0 010 7h-6" stroke="#b8974a"/></svg>
    <h3>International Mining</h3>
    <p>Sed ut perspiciatis unde omnis iste natus error sit voluptatem acidum doloremque laudium</p>
  </div>
  <div class="service" style="left:357px;top:950px">
    <svg width="80" height="80" viewBox="0 0 80 80" fill="none" stroke="#333" stroke-width="2"><rect x="16" y="18" width="48" height="34"/><path d="M10 58h60l-4 6H14z"/><circle cx="40" cy="35" r="9" stroke="#b8974a"/><path d="M40 30v10" stroke="#b8974a"/></svg>
    <h3>Private Investment</h3>
    <p>Sed ut perspiciatis unde omnis iste natus error sit voluptatem acidum doloremque laudium</p>
  </div>
  <div class="service" style="left:600px;top:950px">
    <svg width="80" height="80" viewBox="0 0 80 80" fill="none" stroke="#333" stroke-width="2"><circle cx="36" cy="38" r="24"/><ellipse cx="36" cy="38" rx="10" ry="24"/><path d="M12 38h48M16 26h40M16 50h40"/><circle cx="60" cy="58" r="10" fill="#b8974a" stroke="none"/></svg>
    <h3>Global Experience</h3>
    <p>Sed ut perspiciatis unde omnis iste natus error sit voluptatem acidum doloremque laudium</p>
  </div>
  <div class="service" style="left:846px;top:950px">
    <svg width="80" height="80" viewBox="0 0 80 80" fill="none" stroke="#333" stroke-width="2"><circle cx="32" cy="32" r="14"/><circle cx="32" cy="32" r="20" stroke-dasharray="6 5"/><circle cx="54" cy="50" r="11" stroke="#b8974a"/><path d="M50 64h8M51 68h6" stroke="#b8974a"/></svg>
    <h3>Strategy</h3>
    <p>Sed ut perspiciatis unde omnis iste natus error sit voluptatem acidum doloremque laudium</p>
  </div>
</section>

<section class="story">
  <div class="frame" style="left:98px;top:145px;width:404px;height:404px"></div>
  <div class="photo" style="left:131px;top:176px;width:424px;height:340px;background:linear-gradient(135deg,#5a6a78,#c9c4b8 55%,#3d4650)" role="img" aria-label="Photo of a team discussing charts at a whiteboard"></div>
  <h2 style="left:606px;top:174px">WHO WE ARE</h2>
  <p style="left:606px;top:246px">Sed ut perspiciatis unde omnis iste natus error sit voluptatem accusantium doloremque laudantium, totam rem aperiam, eaque ipsa quae ab illo intore veritatis et quasi architecto beatae vitae dicta sunt explicabo. Nemo enim ipsam voluptatem quia voluptas sit aspernatur aut odit aut fugit, sed quia consequuntur magni dolores eos qui ratione voluptatem sequi nesciunt. Neque porro quisquam est, qui dolorem ipsum quia dolor sit amet, coctetur, adipici velit, sed quia non numquam eius modi</p>
  <div class="btn" style="left:606px;top:470px;width:126px;height:34px;font-size:12px">Read More</div>

  <div class="frame" style="left:692px;top:661px;width:410px;height:410px"></div>
  <div class="photo" style="left:639px;top:694px;width:427px;height:341px;background:linear-gradient(135deg,#c9a27a,#e9e4dc 50%,#8a7a68)" role="img" aria-label="Photo of hands working at a laptop beside printed charts"></div>
  <h2 style="left:131px;top:726px">CORPORATE MISSION</h2>
  <p style="left:131px;top:800px">Sed ut perspiciatis unde omnis iste natus error sit voluptatem accusantium doloremque laudantium, totam rem aperiam, eaque ipsa quae ab illo intore veritatis et quasi architecto beatae vitae dicta sunt explicabo. Nemo enim ipsam voluptatem quia voluptas sit aspernatur aut odit aut fugit, sed quia consequuntur magni dolores eos qui ratione voluptatem sequi nesciunt. Neque porro quisquam est, qui dolorem ipsum quia dolor sit amet, coctetur, adipici velit, sed quia non numquam eius modi</p>
  <div class="btn" style="left:131px;top:1019px;width:126px;height:34px;font-size:12px">Read More</div>
</section>

<section class="clients">
  <h2 class="section-title" style="top:66px;font-size:36px;font-weight:600;letter-spacing:1px"><span class="accent">OUR</span> CLIENTS SAYS</h2>
  <div class="quote" style="left:131px;top:168px">
    <div class="q">“</div>
    <p>Sed ut perspiciatis unde omnis iste natus error sit voluptatem accusantium doloremque laudantium, totam rem aperiam, eaque ipsa quae ab illo inventore veritatis et quasi architecto</p>
    <div class="person"><div class="avatar" role="img" aria-label="Client portrait photo"></div><div><b>Elena R. Marsh</b><small>Halverstone Minerals</small><span class="stars">★★★★★</span></div></div>
  </div>
  <div class="quote" style="left:466px;top:168px">
    <div class="q">“</div>
    <p>Sed ut perspiciatis unde omnis iste natus error sit voluptatem accusantium doloremque laudantium, totam rem aperiam, eaque ipsa quae ab illo inventore veritatis et quasi architecto</p>
    <div class="person"><div class="avatar" role="img" aria-label="Client portrait photo"></div><div><b>Elena R. Marsh</b><small>Halverstone Minerals</small><span class="stars">★★★★★</span></div></div>
  </div>
  <div class="quote" style="left:798px;top:168px">
    <div class="q">“</div>
    <p>Sed ut perspiciatis unde omnis iste natus error sit voluptatem accusantium doloremque laudantium, totam rem aperiam, eaque ipsa quae ab illo inventore veritatis et quasi architecto</p>
    <div class="person"><div class="avatar" role="img" aria-label="Client portrait photo"></div><div><b>Elena R. Marsh</b><small>Halverstone Minerals</small><span class="stars">★★★★★</span></div></div>
  </div>
</section>

<section>
  <h2 class="section-title" style="top:3010px;font-size:36px">LATEST <span class="accent" style="font-weight:600">NEWS</span></h2>
  <article class="news" style="left:131px;top:3119px">
    <div class="img" style="background:linear-gradient(135deg,#3a342c,#7a6a55 50%,#2a2520)" role="img" aria-label="Photo of a mining site with heavy machinery"></div>
    <div class="meta"><div class="date">▦ &nbsp;October 17, 2018</div><div class="title">Quis autem vel eum iure reprehenderit qui in ea voluptate velit</div></div>
  </article>
  <article class="news" style="left:455px;top:3119px">
    <div class="img" style="background:linear-gradient(135deg,#3b5a86,#d9a36a 55%,#5a4a6a)" role="img" aria-label="Photo of a team planning with sticky notes on glass"></div>
    <div class="meta"><div class="date">▦ &nbsp;October 17, 2018</div><div class="title">Quis autem vel eum iure reprehenderit qui in ea voluptate velit</div></div>
  </article>
  <article class="news" style="left:776px;top:3119px">
    <div class="img" style="background:linear-gradient(135deg,#c9a27a,#ebe6df 50%,#8a7a68)" role="img" aria-label="Photo of a laptop and printed financial charts"></div>
    <div class="meta"><div class="date">▦ &nbsp;October 17, 2018</div><div class="title">Quis autem vel eum iure reprehenderit qui in ea voluptate velit</div></div>
  </article>
</section>

<section class="partners">
  <div class="row"><span>QUARRIX</span><span style="font-weight:400">Orvanta</span><span style="font-weight:400;font-size:22px">DELMONT</span><span style="font-weight:400">Keplio</span><span style="font-weight:400;font-size:20px">verdan</span><span>FOWLANE</span></div>
</section>

<footer class="footer">
  <svg class="abs" style="left:0;top:0" width="1200" height="112" viewBox="0 0 1200 112"><rect width="1200" height="112" fill="#f2f2f2"/><polygon points="0,15 1200,0 1200,112 0,112" fill="#161616"/><polygon points="0,15 1200,0 1200,20 0,112" fill="#b8974a"/><polygon points="0,112 1200,20 1200,40 300,112" fill="#8a6f33"/></svg>
  <h4 style="left:131px">Quick <span class="accent">Links</span></h4>
  <ul class="links"><li>Home</li><li>Who We Are</li><li>What We Do</li><li>Corporate Mission</li><li>Vision &amp; Strategy</li><li>Contact Us</li></ul>
  <h4 style="left:346px">Contact <span class="accent">Us</span></h4>
  <div class="contact">
    <div class="row"><svg width="12" height="16" viewBox="0 0 12 16"><path d="M6 0a6 6 0 016 6c0 4-6 10-6 10S0 10 0 6a6 6 0 016-6z" fill="#fff"/><circle cx="6" cy="6" r="2" fill="#161616"/></svg><div>Halverstone Minerals<br>Address<br>Calle Serrano 14, Valladolid</div></div>
    <div class="row"><svg width="12" height="14" viewBox="0 0 12 14"><path d="M1 1c1 6 4 10 10 12l1-3-3-2-2 1C5 8 4 6 4 5l1-2-2-2z" fill="#fff"/></svg><div>Phone : 555 432 0188</div></div>
    <div class="row"><svg width="14" height="12" viewBox="0 0 14 12"><rect x="1" y="1" width="12" height="10" fill="none" stroke="#fff"/><path d="M1 1l6 5 6-5" fill="none" stroke="#fff"/></svg><div>Email : info@halverstoneminerals.com</div></div>
  </div>
  <h4 style="left:664px;font-size:19px;font-weight:500;letter-spacing:1px">SIGN UP TO RECEIVE <span class="accent">EMAIL</span></h4>
  <p class="signup-text">Excepteur sint occaecat cupidatat non proident, sunt in culpa qui officia deserunt mollit anim</p>
  <div class="field">Enter Email<div class="btn">Subscribe</div></div>
  <div class="social"><i></i><i></i><i></i><i></i></div>
  <div class="rule"></div>
  <div class="brand" style="left:131px;top:446px"><div class="mark"></div><span>Halverstone Minerals</span></div>
  <div class="copy">© Copyright 2018 Halverstone Minerals.All rights reserved</div>
</footer>

</body>
</html>
```